life insurance quote website design for lepontdoriole.ca

the web site lepontdoriole.ca need a design. we dont like the actuel one but we are open at all new suggestion. visit us at lepontdoriole.ca and you will understand. the principal concurant is tarifsgarantisnord.ca, calculeo.ca, coutprotecfam.ca. We are a life insurance quote site. we found best price available in the canadien industrie. We absolutly want a design with our form in the front page on the top right side like our concurance, we use wordpress at this time. we want to be able to switch language. and to have a logic form. we want to be able to change the color for each type of insurance quote page.we also need a blog in it to post news. and the site will be SEO accurate.

Target Market(s)

Get client fill the quote form

Industry/Entity Type

Insurance

Number of Pages Required

3 page

Font styles to use
Sans Serif

Requirements
Must have
• logic form on the top right first page
• page template for product info stuff, contact, and who we are, blog
• French site
• custum color
Nice to have
• Wordpress design will be appréciate
• switch language english/french

```html
<!DOCTYPE html>
<html lang="fr">
<head>
<meta charset="utf-8">
<title>Le Pont d'Oriole – Soumission assurance vie</title>
<link href="https://fonts.googleapis.com/css2?family=Open+Sans:wght@400;600;700;800&display=swap" rel="stylesheet">
<style>
:root{
  --red:#d8262b;--red-dark:#a51b1f;--blue:#1e88d8;--blue-light:#4fb3f0;
  --orange:#f39a1e;--green:#5cb85c;--pink:#ec4f7a;
  --ink:#333;--muted:#888;--line:#e3e3e3;--grey:#f2f2f2;--dark:#1d1d1f;--white:#fff;
}
*{box-sizing:border-box;margin:0;padding:0}
html,body{width:1200px;height:2704px;overflow:hidden}
body{font-family:"Open Sans",Arial,sans-serif;color:var(--ink);background:var(--white);font-size:13px;position:relative}
.site-header{height:72px;display:flex;align-items:center;justify-content:space-between;padding:0 40px;position:relative}
.brand{display:flex;align-items:center;gap:10px;font-weight:800;font-size:18px;color:var(--red);white-space:nowrap}
.brand-mark{width:34px;height:34px;background:var(--red)}
.topline{position:absolute;top:6px;right:40px;font-size:10px;color:var(--muted);display:flex;gap:20px;white-space:nowrap}
.nav{display:flex;margin-top:18px}
.nav a{font-size:11px;font-weight:600;text-transform:uppercase;color:var(--ink);text-decoration:none;padding:6px 16px;white-space:nowrap}
.nav a.active{background:var(--red);color:var(--white)}
.hero{height:468px;position:relative;background:linear-gradient(120deg,#5e7f2e 0%,#b6b35b 35%,#e6d6b0 55%,#6f8a3a 100%)}
.hero-box{position:absolute;left:720px;top:110px;width:400px}
.hero h1{font-size:34px;line-height:1.15;font-weight:800;color:var(--white);letter-spacing:1px;text-shadow:0 1px 3px rgba(0,0,0,.3);white-space:nowrap}
.hero h2{font-size:15px;font-weight:700;color:var(--blue-light);text-transform:uppercase;margin:4px 0 20px;white-space:nowrap}
.hero input{display:block;width:100%;height:36px;border:1px solid #ccc;padding:0 12px;margin-bottom:8px;font:inherit}
.btn{display:inline-block;background:var(--red);color:var(--white);border:0;font:inherit;font-weight:700;text-transform:uppercase;white-space:nowrap}
.hero .btn{width:100%;height:38px;font-size:14px}
.assurance{height:240px;background:linear-gradient(var(--red),var(--red-dark));text-align:center;color:var(--white)}
.assurance h3{font-size:20px;font-weight:700;letter-spacing:1px;padding-top:40px}
.products{display:flex;justify-content:space-around;padding:40px 120px 0}
.icon-circle{width:76px;height:76px;border-radius:50%;display:flex;align-items:center;justify-content:center;margin:0 auto;border:4px solid rgba(255,255,255,.6)}
.labels{height:80px;display:flex;justify-content:space-around;align-items:center;padding:0 120px;border-bottom:1px solid var(--line)}
.labels span{width:160px;text-align:center;font-weight:700;font-size:13px;text-transform:uppercase;white-space:nowrap}
.submission{display:flex;gap:40px;padding:40px 60px 40px 80px;height:520px}
.submission .copy{flex:1}
.eyebrow{font-size:13px;color:var(--muted);text-transform:uppercase;font-weight:600}
.section-title{font-size:20px;font-weight:800;text-transform:uppercase;margin:2px 0 14px}
.copy p{font-size:11px;line-height:1.7;color:#666;margin-bottom:12px}
.checklist{list-style:none;margin-top:16px}
.checklist li{font-size:11px;color:#666;padding:4px 0 4px 16px;position:relative}
.checklist li:before{content:"";position:absolute;left:0;top:10px;width:8px;height:2px;background:var(--red)}
.quote{width:420px;border:1px solid var(--line);box-shadow:0 2px 8px rgba(0,0,0,.08);font-size:11px;align-self:flex-start}
.quote-head{background:var(--blue);color:var(--white);text-align:center;font-weight:700;padding:10px;text-transform:uppercase}
.quote-body{padding:16px 18px 20px}
.row{display:flex;align-items:center;gap:8px;margin-bottom:10px}
.row label{width:80px;font-weight:600;white-space:nowrap}
.field{flex:1;height:26px;border:1px solid #ccc;background:var(--white)}
.field.sm{flex:none;width:60px}
.group{font-weight:700;border-bottom:1px solid var(--line);padding-bottom:4px;margin:12px 0 10px}
.captcha{display:flex;justify-content:space-between;align-items:center;margin-top:16px}
.captcha b{font-size:18px;letter-spacing:3px;font-family:"Courier New",monospace}
.captcha .btn{padding:9px 20px;font-size:12px;text-transform:none}
.proceed{background:var(--grey);height:500px;display:flex;gap:40px;padding:50px 80px}
.proceed .copy{flex:1}
.features{display:grid;grid-template-columns:1fr 1fr;gap:18px 24px;margin-top:20px}
.feature{display:flex;gap:10px}
.feature i{width:22px;height:22px;border-radius:50%;background:var(--red);flex:none}
.feature h4{font-size:12px;font-weight:700}
.feature p{font-size:10px;color:#777;line-height:1.5;margin:2px 0 0}
.video{width:480px;height:390px;position:relative;background:linear-gradient(135deg,#c7c9c6,#8e9794 60%,#5d6563)}
.video-badge{position:absolute;left:50%;top:50%;transform:translate(-50%,-50%);display:flex;align-items:center;gap:10px;color:var(--white);font-weight:700;font-size:16px;white-space:nowrap}
.play{width:40px;height:40px;border-radius:50%;border:2px solid var(--white);display:flex;align-items:center;justify-content:center}
.blog{height:460px;padding:30px 80px}
.blog h3{text-align:center;font-size:24px;font-weight:600;margin-bottom:24px}
.cards{display:flex;gap:20px}
.card{flex:1;border:1px solid var(--line)}
.card .thumb{height:150px}
.card .text{padding:12px}
.card h5{font-size:12px;font-weight:700;text-transform:uppercase;margin-bottom:6px}
.card p{font-size:10px;color:#777;line-height:1.5}
.card .meta{border-top:1px solid var(--line);padding:8px 12px;display:flex;justify-content:space-between;font-size:9px;color:var(--muted)}
.card .meta span:first-child{background:var(--red);color:var(--white);padding:2px 6px}
.site-footer{background:var(--dark);height:280px;display:flex;gap:50px;padding:50px 80px;color:#bbb;font-size:10px}
.site-footer h6{color:var(--white);font-size:12px;text-transform:uppercase;margin-bottom:12px;font-weight:700;white-space:nowrap}
.site-footer p{line-height:1.8}
.badge{width:150px;height:90px;background:#3a3a3d}
.news .inbox{display:flex;margin-top:10px}
.news .inbox span{flex:1;height:26px;background:var(--white)}
.news .btn{padding:6px 14px;font-size:10px;text-transform:none}
.social{display:flex;gap:8px;margin-top:14px;justify-content:center}
.social i{width:22px;height:22px;border-radius:50%;border:1px solid #777}
.bottom{height:64px;background:var(--red);color:var(--white);display:flex;align-items:center;justify-content:center;font-size:10px;position:relative}
.bottom .lang{position:absolute;right:40px}
</style>
</head>
<body>
<header class="site-header">
  <div class="brand"><span class="brand-mark"></span>Le Pont d'Oriole</div>
  <div class="topline"><span>1-800-555-0142</span><span>bonjour@primesfictives.test</span><span>Langue ▾</span></div>
  <nav class="nav"><a class="active">Home</a><a>Products</a><a>Submission</a><a>Online Ref</a><a>Contact Us</a></nav>
</header>

<section class="hero" role="img" aria-label="Photo d'une famille souriante allongée dans l'herbe">
  <div class="hero-box">
    <h1>LE PONT D'ORIOLE</h1>
    <h2>Online insurance submission</h2>
    <input placeholder="Your email">
    <input placeholder="Password">
    <button class="btn">Log in</button>
  </div>
</section>

<section class="assurance">
  <h3>THE ASSURANCE OF GETTING THE BEST PRICE</h3>
  <div class="products">
    <div class="icon-circle" style="background:var(--blue)"><svg width="34" height="34" viewBox="0 0 24 24"><path d="M12 21l-8-8a5 5 0 017-7l1 1 1-1a5 5 0 017 7z" fill="#fff"/></svg></div>
    <div class="icon-circle" style="background:var(--orange)"><svg width="34" height="34" viewBox="0 0 24 24"><text x="12" y="19" text-anchor="middle" font-size="20" font-weight="700" fill="#fff" font-family="Open Sans,sans-serif">$</text></svg></div>
    <div class="icon-circle" style="background:var(--green)"><svg width="34" height="34" viewBox="0 0 24 24"><path d="M3 12l9-8 9 8h-3v8h-5v-5h-2v5H6v-8z" fill="#fff"/></svg></div>
    <div class="icon-circle" style="background:var(--pink)"><svg width="34" height="34" viewBox="0 0 24 24"><path d="M9 3h6v6h6v6h-6v6H9v-6H3V9h6z" fill="#fff"/></svg></div>
  </div>
</section>
<div class="labels"><span>Life insurance</span><span>Salary</span><span>Mortgage</span><span>Serious diseases</span></div>

<section class="submission">
  <div class="copy">
    <div class="eyebrow">Online life insurance submission</div>
    <h2 class="section-title">Find the best insurance at the best price!</h2>
    <p>Whether you are looking for life insurance, mortgage insurance or critical illness coverage, we compare the offers of many Canadian insurers to find the price that fits your family and your budget, in just a few minutes.</p>
    <p>Our team of licensed advisors reviews every request carefully. You receive a clear quote, with no obligation, and we guide you until your policy is in force. Simple, fast and free for every applicant.</p>
    <ul class="checklist">
      <li>Permanent life insurance – term life insurance</li>
      <li>Disability insurance – disability coverage</li>
      <li>Mortgage insurance – salary</li>
      <li>Critical illness insurance</li>
    </ul>
  </div>
  <form class="quote">
    <div class="quote-head">Quote request</div>
    <div class="quote-body">
      <div class="row"><label>Products</label><span class="field"></span></div>
      <div class="group">Applicant</div>
      <div class="row"><label>Name</label><span class="field"></span></div>
      <div class="row"><label>Gender</label><span class="field sm"></span><label style="width:50px">Smoker</label><span class="field sm"></span></div>
      <div class="row"><label>Birth date</label><span class="field sm"></span><span class="field sm"></span><span class="field sm"></span></div>
      <div class="row"><label>Email</label><span class="field"></span></div>
      <div class="row"><label>Co-Applicant</label><span class="field sm"></span></div>
      <div class="captcha"><b>DRLXL</b><button class="btn" type="button">Send Now</button></div>
    </div>
  </form>
</section>

<section class="proceed">
  <div class="copy">
    <div class="eyebrow">How to proceed?</div>
    <h2 class="section-title">The online life insurance submission</h2>
    <p>Fill in the quote form, our advisors compare the offers and contact you with the best price available. No cost and no commitment on your part.</p>
    <div class="features">
      <div class="feature"><i></i><div><h4>Financial advisors Security</h4><p>Our certified advisors protect your interests at every step of the process.</p></div></div>
      <div class="feature"><i></i><div><h4>Insurance ?</h4><p>We explain each product clearly so you choose the right coverage.</p></div></div>
      <div class="feature"><i></i><div><h4>Not Overpaying</h4><p>Comparing many insurers means you never pay more than needed.</p></div></div>
      <div class="feature"><i></i><div><h4>How to find</h4><p>Send your request online and get an answer within one business day.</p></div></div>
    </div>
  </div>
  <div class="video" role="img" aria-label="Photo d'un couple rencontrant un conseiller">
    <div class="video-badge">OUR <span class="play"><svg width="14" height="14" viewBox="0 0 10 10"><path d="M2 1l7 4-7 4z" fill="#fff"/></svg></span> VIDEOS</div>
  </div>
</section>

<section class="blog">
  <h3>Our Blog</h3>
  <div class="cards">
    <article class="card"><div class="thumb" role="img" aria-label="Photo de documents d'assurance" style="background:linear-gradient(135deg,#d8d8d8,#9a9a9a)"></div><div class="text"><h5>Permanent Life</h5><p>Whether you are looking for life insurance or mortgage insurance, our tips help you compare offers.</p></div><div class="meta"><span>Jan, 2015</span><span>0 Comments</span></div></article>
    <article class="card"><div class="thumb" role="img" aria-label="Photo d'une main tenant un stylo" style="background:linear-gradient(135deg,#c8a98a,#6d5a4a)"></div><div class="text"><h5>Permanent Life</h5><p>Whether you are looking for life insurance or mortgage insurance, our tips help you compare offers.</p></div><div class="meta"><span>Jan, 2015</span><span>0 Comments</span></div></article>
    <article class="card"><div class="thumb" role="img" aria-label="Photo d'une famille en plein air" style="background:linear-gradient(135deg,#e6d4a8,#8ea35a)"></div><div class="text"><h5>Permanent Life</h5><p>Whether you are looking for life insurance or mortgage insurance, our tips help you compare offers.</p></div><div class="meta"><span>Jan, 2015</span><span>0 Comments</span></div></article>
    <article class="card"><div class="thumb" role="img" aria-label="Photo d'une famille au coucher du soleil" style="background:linear-gradient(180deg,#4c7fb5,#e7a45c)"></div><div class="text"><h5>Permanent Life</h5><p>Whether you are looking for life insurance or mortgage insurance, our tips help you compare offers.</p></div><div class="meta"><span>Jan, 2015</span><span>0 Comments</span></div></article>
  </div>
</section>

<footer class="site-footer">
  <div><div class="badge" role="img" aria-label="Badge de membre"></div></div>
  <div><h6>Our offices</h6><p>Head office: 250 rue Imaginaire, Ville-Exemple<br>Toll free: 1-800-555-0142<br>Phone: 418-555-0168<br>Email: bonjour@primesfictives.test</p></div>
  <div><h6>Hours of operation</h6><p>Monday to Friday: 9 am to 5 pm<br>Saturday: 10 am to 2 pm<br>Sunday: closed</p></div>
  <div class="news" style="flex:1"><h6>Newsletter</h6><p>Get our news and insurance tips directly in your inbox every month.</p><div class="inbox"><span></span><button class="btn">Send</button></div><div class="social"><i></i><i></i><i></i></div></div>
</footer>
<div class="bottom">Copyright © 2015 Company Name. All rights reserved.<span class="lang">FR | EN</span></div>
</body>
</html>
```